Webdesign für Honigmanufaktur
Zielgruppe
Imkerei, Verkauf von Honig und Honigerzeugnissen, so wie Bienenwachskerzen.
Zielgruppe sind vermutlich Frauen im mittleren bis gehobenen Alter.
Aufgabenstellung
Es gibt ein Firmenlogo.
Ich bevorzuge als Grundfarbe weiß, lasse mich aber von guten Einfällen gerne überraschen.
Die Website www.kelvaroni.at finde ich sehr ansprechend.
Nur ohne Musik.
Ohne Deutsch/Englisch Auswahl.
Es soll danach Word press verwendet werden.

```html
<!DOCTYPE html>
<html lang="de">
<head>
<meta charset="utf-8">
<title>Honigmanufaktur Tannenhain</title>
<link href="https://fonts.googleapis.com/css2?family=Raleway:wght@300;400;700;800;900&display=swap" rel="stylesheet">
<style>
  :root {
    --brown: #4a2a0c;
    --amber: #f2a43a;
    --text: #6b6b6b;
    --white: #ffffff;
  }
  * { margin: 0; padding: 0; box-sizing: border-box; }
  html, body { width: 1200px; height: 4173px; overflow: hidden; background: var(--white); }
  body { position: relative; font-family: 'Raleway', sans-serif; }

  .brand {
    position: absolute; left: 83px; top: 150px; width: 400px;
    display: flex; flex-direction: column; align-items: center; gap: 30px;
  }
  .brand-mark { width: 110px; height: 110px; background: var(--amber); }
  .brand-name {
    font-weight: 800; font-size: 40px; line-height: 1.15; color: var(--brown);
    text-align: center; letter-spacing: 1px;
  }

  .menu-toggle { position: absolute; left: 973px; top: 133px; width: 154px; height: 94px; }
  .menu-toggle span { position: absolute; left: 0; width: 100%; height: 14px; background: var(--brown); }
  .menu-toggle span:nth-child(1) { top: 0; }
  .menu-toggle span:nth-child(2) { top: 40px; }
  .menu-toggle span:nth-child(3) { top: 80px; }

  .honey-visual { position: absolute; left: 683px; top: 317px; width: 517px; height: 533px; }
  .hero-visual { position: absolute; left: 0; top: 667px; width: 1200px; height: 890px; }

  .intro { position: absolute; left: 100px; top: 1730px; width: 1020px; }
  .intro-title {
    font-weight: 900; font-size: 86px; line-height: 122px; color: var(--brown); text-transform: uppercase;
  }
  .intro-title .accent { display: block; color: var(--amber); }
  .intro-text {
    margin-top: 98px; font-weight: 400; font-size: 48px; line-height: 52.5px; color: var(--text);
    hyphens: auto;
  }
  .intro-text + .intro-text { margin-top: 52px; }

  .more-link {
    position: absolute; left: 100px; top: 3557px; height: 143px; display: flex; align-items: center; gap: 105px;
    text-decoration: none;
  }
  .more-link-label { font-weight: 800; font-size: 58px; color: var(--brown); text-transform: uppercase; }
  .more-link-icon { width: 153px; height: 143px; }

  .site-footer {
    position: absolute; left: 100px; top: 3915px; width: 1020px;
    font-weight: 400; font-size: 41px; line-height: 52px; color: var(--text);
  }
</style>
</head>
<body>
  <header class="site-header">
    <div class="brand">
      <div class="brand-mark"></div>
      <div class="brand-name">HONIGMANUFAKTUR<br>TANNENHAIN</div>
    </div>
    <div class="menu-toggle" aria-label="Menü"><span></span><span></span><span></span></div>
  </header>

  <svg class="honey-visual" viewBox="0 0 517 533" role="img" aria-label="Honiglöffel aus Holz, von dem Honig tropft">
    <defs>
      <linearGradient id="honeyGrad" x1="0" y1="0" x2="0" y2="1">
        <stop offset="0" stop-color="#e3a354"/>
        <stop offset="1" stop-color="#f4b51c"/>
      </linearGradient>
    </defs>
    <rect x="0" y="0" width="517" height="533" fill="url(#honeyGrad)" rx="40"/>
  </svg>

  <svg class="hero-visual" viewBox="0 0 1200 890" role="img" aria-label="Nahaufnahme einer Biene auf einer gelben Blüte in Wabenform">
    <defs>
      <linearGradient id="beeGrad" x1="0" y1="0" x2="1" y2="1">
        <stop offset="0" stop-color="#e9b934"/>
        <stop offset="0.55" stop-color="#c77a1e"/>
        <stop offset="1" stop-color="#f0c23c"/>
      </linearGradient>
    </defs>
    <polygon points="167,0 500,0 667,300 1200,300 1200,890 0,890 0,600 167,600 10,300" fill="url(#beeGrad)"/>
    <polyline points="10,300 167,600 500,600 667,300" fill="none" stroke="#ffffff" stroke-width="4"/>
    <polyline points="500,600 667,890" fill="none" stroke="#ffffff" stroke-width="4"/>
    <polyline points="667,300 500,600" fill="none" stroke="#ffffff" stroke-width="4"/>
    <polyline points="667,890 1000,890 1200,560" fill="none" stroke="#ffffff" stroke-width="4"/>
  </svg>

  <main class="intro">
    <h1 class="intro-title">Honigmanufaktur<span class="accent">Tannenhain</span></h1>
    <p class="intro-text">Lorem ipsum dolor sit amet, consetetur sadipscing elitr, sed diam nonumy eirmod tempor invidunt ut labore et dolore magna aliquyam erat, sed diam voluptua. At vero eos et accusam et justo duo dolores et ea rebum. Stet clita kasd gubergren, no sea takimata sanctus est Lorem ipsum dolor sit amet. Lorem ipsum dolor sit amet, consetetur sadipscing elitr, sed diam nonumy eirmod tempor invidunt ut labore et dolore magna aliquyam erat, sed diam voluptua. At vero eos et accusam et justo duo dolores et ea rebum. Stet clita kasd gubergren, no sea takimata sanctus est Lorem ipsum dolor sit amet.</p>
    <p class="intro-text">Lorem ipsum dolor sit amet, consetetur sadipscing elitr, sed diam nonumy eirmod tempor invidunt ut labore et dolore magna aliquyam erat, sed diam voluptua. At vero eos et accusam et justo duo dolores et ea rebum.</p>
  </main>

  <a class="more-link" href="#">
    <span class="more-link-label">Mehr erfahren</span>
    <svg class="more-link-icon" viewBox="0 0 153 143" aria-hidden="true">
      <polygon points="40,6 113,6 147,71.5 113,137 40,137 6,71.5" fill="none" stroke="var(--amber)" stroke-width="9"/>
      <polyline points="66,48 90,71.5 66,95" fill="none" stroke="var(--brown)" stroke-width="12" stroke-linecap="square"/>
    </svg>
  </a>

  <footer class="site-footer">
    Copyright 2018 - Honigmanufaktur Tannenhain -<br>
    Alle Rechte vorbehalten<br>
    Impressum | Datenschutzerklärung
  </footer>
</body>
</html>
```